$5 Quest Website Required

I am looking for someone to develop a website akin to the simplicity of www.boxlantern.example with a video in the center or a tab that permits one to "Accept the Challenge."

Incorporates our logo and is used to promote our "$5 Quest Program."

Please see attachments, but we are igniting entrepreneurial spirit among our nation's youth through this interactive and intensive program!

There should be a way to navigate to other sections of the site including:

About
Why
Request $5 Quest Packet
Success Stories
Partners
Link to Norvik Holdings
Updates

Thanks to all in advance!

Looking forward to working with you!

Good feel of what we are looking for in terms of "feel"

http://www.thebrightripple.example/

Thank you,

RB

Please make note of this website, we are going for a feel that is akin to this and less modern and professional...more abstract and interactive...but of course include space for our video:

Colors, feel, imagery, is great. Keep your formats, but bring on the feel!

Thank you all for your hard work and patience.

Thank you all for your hard work thus far.

Meanwhile, please understand that the $5 Quest is young, youthful, full of challenge and vitality, it is a competition among students from high school and universities.  The websites you have delivered are too corporate, stale, and standard.  I'm looking for something that is fresh, different, like www.thebrightripple.example.

Symbols, cartoonish, but serious, down to business and save the world one $5 bill at a time.  The logo can be used as a theme...the colors, the feel.

Video space for explanation on the $5 Quest front and center.  With leaves, $ signs, colorful colors, etc.

Visual needs to be compelling to Join the Challenge! Although Norvik Holdings and the tree is a parent company; $5 Quest is separate and Norvik Holdings should only be mentioned as a link.

PixelHarbor.example in regard to simplicity; and www.thebrightripple.example in terms of style.

Thank you,

Raphael

Like the designs that have been submitted; we are almost there.

Target Market(s)

Professors, students, teachers, parents and NGO leaders who wish to use our program as a way to inspire leadership/entrepreneurship/fundraise for their causes.

Requirements
Must have
• Place for the video, front and center
Include logo
Forsight for blogging, message, etc.
Nice to have
• Plan "buckets" to include"
Explanation Video
Two pamphlets
Contract
FAQs
Website with Blog, voting, registration, video upload, etc.
Flyer perfected
Parable...symbol of our life
Photos
Stats included
Testimonials
Organizations that have used (TKWLM, North Brook Lodge, Marlowton High)
Sponsors (Open Lantern, Copperleaf Learningfield)
Photos from events

I understand this takes coding and such, but want you to be aware of the long term vision for it!

```html
<!DOCTYPE html>
<html lang="en">
<head>
<meta charset="utf-8">
<title>$5 Quest</title>
<link rel="stylesheet" href="https://fonts.googleapis.com/css2?family=Roboto+Condensed:wght@400;500&family=Arimo:wght@400&family=PT+Sans:wght@400&display=swap">
<style>
  :root {
    --cream: #fbf3dc;
    --cream-deep: #efe1bb;
    --green: #0f9142;
    --green-dark: #0b7434;
    --orange: #f7931e;
    --gold-line: #f3cd3a;
    --text: #5b5b5b;
    --ink: #222222;
    --nav-grey: #4d4d4d;
    --frame-grey: #d9d9d9;
    --dot-grey: #b9b2a0;
  }
  * { box-sizing: border-box; margin: 0; padding: 0; }
  html, body { width: 1200px; height: 990px; overflow: hidden; }
  body {
    position: relative;
    background: var(--cream);
    font-family: "Arimo", Arial, sans-serif;
    color: var(--text);
  }
  .backdrop {
    position: absolute; inset: 0;
    background:
      radial-gradient(ellipse 420px 300px at 600px 140px, rgba(255,255,255,0.85), rgba(255,255,255,0) 70%),
      radial-gradient(ellipse 260px 340px at 220px 640px, rgba(214,196,150,0.35), rgba(214,196,150,0) 70%),
      radial-gradient(ellipse 300px 380px at 880px 560px, rgba(214,196,150,0.35), rgba(214,196,150,0) 70%),
      radial-gradient(ellipse 220px 220px at 830px 190px, rgba(214,196,150,0.3), rgba(214,196,150,0) 70%),
      linear-gradient(180deg, #fdf8ea 0%, var(--cream) 40%, #f8eed3 100%);
  }

  .utility-bar { position: absolute; top: 0; right: 34px; display: flex; align-items: stretch; height: 29px;
    font-family: "Roboto Condensed", sans-serif; font-weight: 500; font-size: 16px; color: var(--ink); }
  .utility-bar a { color: inherit; text-decoration: none; display: flex; align-items: center; padding: 0 10px; }
  .utility-bar .signin { background: #efefef; margin-left: 2px; padding: 0 16px; }
  .utility-bar .language { background: var(--green); color: #fff; font-size: 14px; margin-left: 5px; padding: 0 10px; gap: 14px; border-radius: 0 0 2px 2px; }

  .brand { position: absolute; top: 48px; left: 0; width: 1200px; display: flex; justify-content: center; align-items: center; gap: 16px; }
  .brand-mark { width: 92px; height: 92px; border-radius: 50%; background: var(--green); }
  .brand-name { font-family: "PT Sans", sans-serif; font-size: 60px; color: var(--nav-grey); line-height: 1; }

  .main-nav { position: absolute; top: 232px; left: 0; width: 1200px; display: flex; justify-content: center; align-items: center;
    font-family: "Roboto Condensed", sans-serif; font-weight: 500; font-size: 22px; letter-spacing: 0.4px; }
  .main-nav a { color: var(--nav-grey); text-decoration: none; }
  .main-nav a.current { color: var(--green); }
  .main-nav .sep { width: 6px; height: 6px; border-radius: 50%; background: var(--green); margin: 0 20px; }
  .nav-rule { position: absolute; top: 276px; left: 24px; width: 1152px; height: 1px; background: var(--gold-line); }

  .section-title { font-family: "PT Sans", sans-serif; font-size: 22px; font-weight: 400; line-height: 1; padding-bottom: 10px;
    border-bottom: 2px dotted var(--ink); }
  .section-title .accent-orange { color: var(--orange); }
  .section-title .accent-green { color: var(--green); }

  .welcome { position: absolute; top: 331px; left: 24px; width: 314px; }
  .welcome p { font-size: 15px; line-height: 21.6px; text-align: justify; margin-top: 6px; }
  .welcome .section-title { margin-bottom: 16px; }

  .testimonials { position: absolute; top: 331px; left: 972px; width: 204px; }
  .testimonials .section-title { text-align: right; border-bottom-color: #555; margin-bottom: 22px; }
  .quote { width: 170px; font-size: 15px; line-height: 19.5px; text-align: justify; }
  .quote.first { margin-left: 12px; }
  .quote.second { margin-left: 8px; margin-top: 26px; }
  .quote-author { text-align: right; font-size: 14.5px; margin-top: 12px; letter-spacing: 0.3px; }

  .video-frame { position: absolute; top: 298px; left: 394px; width: 532px; height: 444px;
    border: 1px solid var(--gold-line); border-radius: 6px; padding: 6px; background: rgba(255,255,255,0.4);
    box-shadow: 0 14px 18px -10px rgba(0,0,0,0.35); }
  .video-screen { width: 100%; height: 100%; border: 7px solid var(--frame-grey); background: #fff; position: relative;
    box-shadow: inset 0 0 6px rgba(0,0,0,0.08); }
  .play-button { position: absolute; left: 170px; top: 88px; }
  .video-label { position: absolute; left: 0; width: 100%; top: 305px; text-align: center;
    font-family: "Roboto Condensed", sans-serif; font-weight: 500; font-size: 32px; color: var(--ink); letter-spacing: -0.5px; transform: scaleY(1.1); }

  .cta { position: absolute; top: 788px; left: 306px; width: 694px; height: 65px; }
  .cta-label { position: absolute; top: 0; left: 138px; width: 398px; height: 65px; display: flex; align-items: center; justify-content: center;
    font-family: "Arimo", sans-serif; font-size: 23px; color: #fff; text-decoration: none; letter-spacing: 0.2px; }

  .footer-rule { position: absolute; top: 902px; left: 24px; width: 1152px; border-top: 2px dotted #cfc7b3; }
  .footer-brand { position: absolute; top: 932px; left: 41px; display: flex; align-items: center; gap: 8px; }
  .footer-brand .brand-mark { width: 30px; height: 30px; }
  .footer-brand .brand-name { font-size: 25px; }
  .footer-links { position: absolute; top: 926px; right: 40px; display: flex; gap: 22px; font-size: 13.5px; }
  .footer-links a { color: var(--ink); text-decoration: none; }
  .copyright { position: absolute; top: 953px; right: 40px; font-size: 13px; color: var(--ink); }
</style>
</head>
<body>
  <div class="backdrop" role="img" aria-label="Soft sunlit background of stacked gold coins"></div>

  <nav class="utility-bar">
    <a href="#">FAQ</a>
    <a href="#" class="signin">SIGNIN</a>
    <a href="#" class="language">LANGUAGE
      <svg width="12" height="10" viewBox="0 0 12 10"><polygon points="0,0 12,0 6,10" fill="#fff"/></svg>
    </a>
  </nav>

  <header class="brand">
    <span class="brand-mark"></span>
    <span class="brand-name">$5 Quest</span>
  </header>

  <nav class="main-nav">
    <a href="#" class="current">HOME</a><span class="sep"></span>
    <a href="#">ABOUT US</a><span class="sep"></span>
    <a href="#">WHY WE ARE?</a><span class="sep"></span>
    <a href="#">SUCCESS STORIES</a><span class="sep"></span>
    <a href="#">PARTNERS</a><span class="sep"></span>
    <a href="#">NORVIK HOLDINGS</a>
  </nav>
  <div class="nav-rule"></div>

  <section class="welcome">
    <h2 class="section-title"><span class="accent-orange">WELCOME TO </span><span class="accent-green">$5 QUEST</span></h2>
    <p>Lorem ipsum dolor sit amet, consectetur adipiscing elit. Curabitur eu nisl odio. Cras egestas turpis in mi feugiat vel tincidunt arcu accumsan. Phasellus non posuere eros. Aenean consectetur.</p>
    <p>sapien in elit luctus ac posuere purus placerat. Aliquam turpis lorem,.</p>
    <p>Donec fermentum sodales erat, quis consequat nisi ornare eget. Duis volutpat justo ut ante imperdiet feugiat.&nbsp; fermentum sodales erat, quis consequat nisi ornare eget. Duis volutpat justo ut ante imperdiet feugiat.</p>
    <p>sapien in elit luctus ac posuere purus placerat. Aliquam turpis lorem,.</p>
  </section>

  <section class="video-frame">
    <div class="video-screen">
      <svg class="play-button" width="176" height="176" viewBox="0 0 176 176" aria-label="Play video">
        <defs>
          <linearGradient id="playShade" x1="0" y1="0" x2="0" y2="1">
            <stop offset="0" stop-color="#3a3a3a"/>
            <stop offset="1" stop-color="#0d0d0d"/>
          </linearGradient>
        </defs>
        <circle cx="88" cy="88" r="87" fill="url(#playShade)"/>
        <polygon points="71,54 71,122 118,88" fill="#c9c9c9"/>
      </svg>
      <div class="video-label">WATCH VIDEO</div>
    </div>
  </section>

  <aside class="testimonials">
    <h2 class="section-title"><span class="accent-green">Client </span><span class="accent-orange">Testimonials</span></h2>
    <p class="quote first">Lorem ipsum dolor sit amsectetur adipiscing elit. Curabitur eu nisl odio. dolor sit amsectetur u nisl odio.</p>
    <p class="quote-author">- LOREM IPSUM</p>
    <p class="quote second">Lorem ipsum dolor sit amsectetur adipiscing elit. Curabitur eu nisl odio. dolor sit amsectetur u nisl odio.</p>
    <p class="quote-author">- LOREM IPSUM</p>
  </aside>

  <div class="cta">
    <svg width="694" height="65" viewBox="0 0 694 65">
      <line x1="0" y1="34" x2="145" y2="34" stroke="#0f9142" stroke-width="2" stroke-dasharray="6 5"/>
      <line x1="530" y1="34" x2="694" y2="34" stroke="#0f9142" stroke-width="2" stroke-dasharray="6 5"/>
      <polygon points="154,0 522,0 536,65 138,65" fill="#0f9142"/>
    </svg>
    <a href="#" class="cta-label">ACCEPT THE CHALLENGE</a>
  </div>

  <div class="footer-rule"></div>
  <footer>
    <div class="footer-brand">
      <span class="brand-mark"></span>
      <span class="brand-name">$5 Quest</span>
    </div>
    <nav class="footer-links">
      <a href="#">Home</a>
      <a href="#">About Us</a>
      <a href="#">Success Stories</a>
      <a href="#">Partners</a>
      <a href="#">Norvik Holdings</a>
      <a href="#">Terms</a>
      <a href="#">Privacy Policy</a>
    </nav>
    <p class="copyright">All Rights reserved @ $5quest</p>
  </footer>
</body>
</html>
```